Business Card Design - Amberfield Court

We are looking at a new design for our business cards that has a modern and professional look. We run a residential aged care facility focussing on the care of residents. The cards will be used for potential clients, consultants and business opportunities in this sector. Blue and white is our main colours and would to see these colours incorporated in the design.
Industry/Entity Type
Business
Contact Information for Business Card
Amberfield Court, Darren Walsh, dwalsh@amberfieldcourt.com.au, Finance Manager, 0472 639 208, BCom, 37 Marrabel Crescent, Brindle Vale, Qld 4093.
Look and feel
Each slider illustrates characteristics of the customer's brand and the style your logo design should communicate.

```html
<!DOCTYPE html>
<html lang="en">
<head>
<meta charset="utf-8">
<title>Amberfield Court – Business Card</title>
<link rel="stylesheet" href="https://fonts.googleapis.com/css2?family=Open+Sans:wght@400;600;700&display=swap">
<style>
  :root {
    --backdrop: #2e2f31;
    --card-navy: #1f3b4b;
    --card-blue: #00aeef;
    --mark-blue: #4f7f9c;
    --white: #ffffff;
    --soft-white: #e8f3f8;
  }
  * { box-sizing: border-box; margin: 0; padding: 0; }
  html, body {
    width: 1200px; height: 900px; overflow: hidden;
    background: var(--backdrop);
    font-family: "Open Sans", Arial, sans-serif;
  }
  .canvas { position: relative; width: 1200px; height: 900px; }
  .card {
    position: absolute; left: 280px; width: 640px; height: 366px;
    border-radius: 26px; overflow: hidden;
  }
  .card-back { top: 56px; background: var(--card-navy); }
  .card-front { top: 478px; background: var(--card-blue); color: var(--white); }

  .brand {
    position: absolute; display: flex; align-items: center; gap: 14px;
    font-weight: 600; letter-spacing: 0.04em; text-transform: uppercase;
  }
  .brand-dot { border-radius: 50%; flex: none; }
  .card-back .brand {
    left: 50%; top: 50%; transform: translate(-50%, -50%);
    color: var(--soft-white); font-size: 34px;
  }
  .card-back .brand-dot { width: 34px; height: 34px; background: var(--mark-blue); }
  .card-front .brand {
    right: 40px; top: 44px; color: var(--white); font-size: 20px; gap: 10px;
  }
  .card-front .brand-dot { width: 20px; height: 20px; background: var(--white); }

  .divider {
    position: absolute; left: 40px; right: 40px; top: 176px;
    height: 1px; background: var(--white);
  }
  .address {
    position: absolute; right: 40px; top: 118px; text-align: right;
    font-size: 15px; line-height: 1.45;
  }
  .contact { position: absolute; left: 40px; bottom: 34px; }
  .person-name { font-size: 28px; font-weight: 700; letter-spacing: 0.02em; line-height: 1.1; }
  .person-role {
    font-size: 14px; text-transform: uppercase; letter-spacing: 0.03em;
    padding-bottom: 8px; border-bottom: 1px solid var(--white); margin-bottom: 10px;
  }
  .contact-line { display: flex; align-items: center; gap: 10px; font-size: 15px; line-height: 1.6; }
  .contact-line svg { width: 14px; height: 14px; flex: none; }
</style>
</head>
<body>
<main class="canvas">
  <section class="card card-back" aria-label="Card back">
    <div class="brand"><span class="brand-dot"></span>Amberfield Court</div>
  </section>

  <section class="card card-front" aria-label="Card front">
    <div class="brand"><span class="brand-dot"></span>Amberfield Court</div>
    <address class="address" style="font-style:normal">37 Marrabel Crescent<br>Brindle Vale, Qld 4093</address>
    <div class="divider"></div>
    <div class="contact">
      <div class="person-name">DARREN WALSH</div>
      <div class="person-role">Finance Manager(BCom)</div>
      <div class="contact-line">
        <svg viewBox="0 0 24 24" aria-hidden="true"><path fill="#fff" d="M6.6 10.8a15.1 15.1 0 0 0 6.6 6.6l2.2-2.2a1 1 0 0 1 1-.25 11.4 11.4 0 0 0 3.6.57 1 1 0 0 1 1 1V20a1 1 0 0 1-1 1A17 17 0 0 1 3 4a1 1 0 0 1 1-1h3.5a1 1 0 0 1 1 1c0 1.25.2 2.45.57 3.57a1 1 0 0 1-.25 1z"/></svg>
        <span>0472 639 208</span>
      </div>
      <div class="contact-line">
        <svg viewBox="0 0 24 24" aria-hidden="true"><rect x="2.5" y="5" width="19" height="14" rx="1.5" fill="none" stroke="#fff" stroke-width="2"/><path d="M3 6l9 7 9-7" fill="none" stroke="#fff" stroke-width="2"/></svg>
        <span>dwalsh@amberfieldcourt.com.au</span>
      </div>
    </div>
  </section>
</main>
</body>
</html>
```